Letterhead, stationery and email signature for construction business

I need the letterhead, stationery and email signature designs for a construction business. I want them to have a corporate feel to them.

I've attached the logo for reference.

```html
<!DOCTYPE html>
<html lang="en">
<head>
<meta charset="utf-8">
<title>Norvale Projects – Business Card</title>
<link rel="stylesheet" href="https://fonts.googleapis.com/css2?family=Roboto:wght@400;500;700&display=swap">
<style>
  :root {
    --backdrop: #1a1a1c;
    --card-white: #fbfbfa;
    --brand-blue: #3d64b0;
    --back-blue: #4468b1;
    --back-mark: #8fa6dd;
    --slate: #5d6270;
    --text-grey: #5f6168;
  }
  * { box-sizing: border-box; margin: 0; padding: 0; }
  html, body { width: 1200px; height: 780px; overflow: hidden; }
  body {
    background: var(--backdrop);
    font-family: "Roboto", Arial, sans-serif;
    position: relative;
  }
  .card {
    position: absolute;
    top: 235px;
    width: 540px;
    height: 310px;
    overflow: hidden;
  }
  .card--front { left: 45px; background: var(--card-white); }
  .card--back { left: 615px; background: var(--back-blue); }

  .corner-bands { position: absolute; inset: 0; }

  .holder { position: absolute; left: 44px; top: 70px; }
  .holder__name {
    color: var(--brand-blue);
    font-weight: 700;
    font-size: 19px;
    letter-spacing: 0.2px;
  }
  .holder__title {
    color: var(--text-grey);
    font-weight: 500;
    font-size: 14px;
    margin-top: 2px;
  }
  .contact-list { list-style: none; margin-top: 12px; }
  .contact-list li {
    display: flex;
    align-items: center;
    gap: 8px;
    color: var(--text-grey);
    font-size: 14px;
    line-height: 19px;
  }
  .contact-list svg { width: 12px; height: 12px; flex: none; }

  .wordmark {
    position: absolute;
    display: flex;
    align-items: center;
    gap: 10px;
    font-weight: 700;
    text-transform: uppercase;
  }
  .wordmark__square { flex: none; }
  .wordmark__text { line-height: 1; }
  .wordmark__text span { display: block; }

  .card--front .wordmark { left: 300px; top: 118px; color: var(--brand-blue); }
  .card--front .wordmark__square { width: 34px; height: 34px; background: var(--brand-blue); }
  .card--front .wordmark__name { font-size: 32px; letter-spacing: 0.5px; }
  .card--front .wordmark__sub { font-size: 13px; letter-spacing: 10px; margin-top: 4px; }

  .address {
    position: absolute;
    left: 262px;
    top: 205px;
    color: var(--text-grey);
    font-size: 13.5px;
    line-height: 19px;
  }

  .card--back .wordmark { left: 120px; top: 114px; color: var(--back-mark); }
  .card--back .wordmark__square { width: 42px; height: 42px; background: var(--back-mark); }
  .card--back .wordmark__name { font-size: 40px; letter-spacing: 0.5px; }
  .card--back .wordmark__sub { font-size: 16px; letter-spacing: 13px; margin-top: 5px; }
</style>
</head>
<body>

  <section class="card card--front" aria-label="Business card, front">
    <svg class="corner-bands" viewBox="0 0 540 310" width="540" height="310" aria-hidden="true">
      <polygon fill="var(--slate)" points="0,160 14,146 14,296 130,296 116,310 0,310"/>
      <polygon fill="var(--brand-blue)" points="540,150 526,164 526,14 412,14 426,0 540,0"/>
    </svg>

    <div class="holder">
      <p class="holder__name">MARCUS HALE</p>
      <p class="holder__title">President</p>
      <ul class="contact-list">
        <li>
          <svg viewBox="0 0 12 12" aria-hidden="true"><path fill="var(--brand-blue)" d="M2.4 0.8l2 2.2-1 1.4c.6 1.4 1.7 2.6 3.2 3.3l1.4-1 2.2 2-1.2 2c-4.4-.6-7.8-4-8.4-8.4z"/></svg>
          (555) 318-4400
        </li>
        <li>
          <svg viewBox="0 0 12 12" aria-hidden="true"><rect x="3" y="1" width="6" height="3" fill="var(--brand-blue)"/><rect x="1" y="4.5" width="10" height="5" rx="1" fill="var(--brand-blue)"/><rect x="3" y="8" width="6" height="3" fill="var(--brand-blue)"/></svg>
          (555) 318-4417
        </li>
        <li>
          <svg viewBox="0 0 12 12" aria-hidden="true"><rect x="0.8" y="2.2" width="10.4" height="7.6" fill="none" stroke="var(--brand-blue)" stroke-width="1.2"/><path d="M0.8 2.2L6 6.6 11.2 2.2M0.8 9.8L4.4 5.6M11.2 9.8L7.6 5.6" fill="none" stroke="var(--brand-blue)" stroke-width="1"/></svg>
          info@norvale.com
        </li>
        <li>
          <svg viewBox="0 0 12 12" aria-hidden="true"><g fill="none" stroke="var(--brand-blue)" stroke-width="1"><circle cx="6" cy="6" r="5.2"/><ellipse cx="6" cy="6" rx="2.3" ry="5.2"/><path d="M0.8 6h10.4M1.6 3.3h8.8M1.6 8.7h8.8"/></g></svg>
          www.norvale.com
        </li>
      </ul>
    </div>

    <div class="wordmark">
      <span class="wordmark__square" aria-hidden="true"></span>
      <p class="wordmark__text">
        <span class="wordmark__name">Norvale</span>
        <span class="wordmark__sub">Projects</span>
      </p>
    </div>

    <address class="address" style="font-style: normal;">
      Norvale Project, Ltd.<br>
      Ashby House, 42 Carlton<br>
      Rd, Bristol BS8 4QT
    </address>
  </section>

  <section class="card card--back" aria-label="Business card, back">
    <div class="wordmark">
      <span class="wordmark__square" aria-hidden="true"></span>
      <p class="wordmark__text">
        <span class="wordmark__name">Norvale</span>
        <span class="wordmark__sub">Projects</span>
      </p>
    </div>
  </section>

</body>
</html>
```